Business Cards for IT Consulting Company (Managed Service Provider)

I am looking to have some business cards printed and would like some designs. We are an IT Consulting company based in Vancouver BC. I would like a nice clean and modern look to the cards. I have uploaded all the versions of my logo so parts can be used as needed. Here is a snippit from our website homepage:

Quillbrook Networks Ltd. is an IT Solutions Partner located in Vancouver BC, Canada. We offer IT solutions and support to customers in the greater Vancouver Area. With expertise in Microsoft platforms, as well as Linux and Mac OSX and over 12 years experience in the IT industry, Quillbrook Networks is dedicated to offering our clients top quality service and products. We take pride in the solutions we offer our customers. The greatest compliment a client can give us is to recommend our services.

Quillbrook Networks Ltd. offers a wide range of IT services from onsite service to remote support and managed service solutions. This allows clients to choose the support path that best suits their company’s needs. Supporting many different sized companies from small to enterprise level over the past 12 years Quillbrook Networks has the experience and expertise needed to ensure things run smoothly. Allowing our clients to focus on doing business.

Revolutionizing the way IT services are delivered.

Quillbrook Networks is dedicated to providing our clients with IT solutions that work and grow with them for years to come. This philosophy helps save money in the long run instead of replacing equipment constantly. Far too often IT solutions are not well thought out and while possibly solving the problem at hand, require replacement due to growth or quality within a very short time frame. Quillbrook Networks takes pride in providing solutions that will last and be able to accommodate growth without the need for replacement.

Industry/Entity Type

Information Technology

Contact Information for Business Card

Quillbrook Networks Ltd.
(Employee Name)
Eml: (Employees Email Address)
Web: quillbrook.me
Ph: 604-555-0148

Font styles to use
Serif
Sans Serif

Requirements
Must have
• The Company logo and company colors.
Nice to have
• - Our tag line: "Revolutionizing IT Services" or "Revolutionizing the way IT services are delivered."
• - Also I really like the idea of nature and technology together blending which is sort of where my logo came from so integrating that somehow onto the business cards would be great.

```html
<!DOCTYPE html>
<html lang="en">
<head>
<meta charset="utf-8">
<title>Quillbrook Networks Ltd. — Business Cards</title>
<link rel="stylesheet" href="https://fonts.googleapis.com/css2?family=Montserrat:wght@400;500;600;700&display=swap">
<style>
  :root {
    --brand-blue: #16a8e6;
    --brand-blue-pale: #e3f4fc;
    --ink-grey: #54565a;
    --band-grey: #5f6164;
    --card-white: #ffffff;
    --backdrop: #e6e7e9;
  }
  * { box-sizing: border-box; margin: 0; padding: 0; }
  html, body {
    width: 1200px; height: 900px; overflow: hidden;
    background: var(--backdrop);
    font-family: "Montserrat", sans-serif;
  }
  .canvas { position: relative; width: 1200px; height: 900px; }
  .card {
    position: absolute; width: 700px; height: 400px;
    background: var(--card-white); overflow: hidden;
    box-shadow: 0 6px 18px rgba(0,0,0,0.12);
  }
  .card--front { left: 60px; top: 45px; }
  .card--back { left: 440px; top: 470px; }

  /* Front */
  .front-brand {
    position: absolute; left: 150px; top: 150px;
    display: flex; align-items: center; gap: 22px;
  }
  .brand-square {
    width: 64px; height: 64px; border: 5px solid var(--brand-blue);
  }
  .brand-name {
    font-weight: 600; color: var(--brand-blue);
    font-size: 38px; line-height: 1.05; letter-spacing: 0.5px;
  }
  .tagline {
    margin-top: 10px; font-size: 16px; font-weight: 500;
    color: var(--ink-grey); letter-spacing: 1.2px;
  }

  /* Back */
  .back-art { position: absolute; left: 0; top: 0; width: 700px; height: 400px; }
  .corner-tab {
    position: absolute; right: 0; top: 70px;
    width: 26px; height: 34px; background: var(--band-grey);
  }
  .back-info {
    position: absolute; right: 46px; top: 48px; text-align: right;
  }
  .back-info .brand-name { font-size: 30px; }
  .person-name {
    margin-top: 26px; font-size: 22px; font-weight: 700;
    color: var(--brand-blue); letter-spacing: 1.5px;
  }
  .person-role {
    font-size: 12px; font-weight: 600; color: var(--ink-grey);
    letter-spacing: 1.5px; margin-top: 2px;
  }
  .contact-list { list-style: none; margin-top: 22px; }
  .contact-list li {
    display: flex; justify-content: flex-end; align-items: center; gap: 10px;
    font-size: 14px; font-weight: 500; color: var(--ink-grey);
    letter-spacing: 0.6px; line-height: 1.75;
  }
  .contact-list svg { width: 12px; height: 12px; flex: none; }
</style>
</head>
<body>
<main class="canvas">

  <section class="card card--front" aria-label="Card front">
    <div class="front-brand">
      <div class="brand-square"></div>
      <div>
        <div class="brand-name">Quillbrook Networks Ltd.</div>
        <div class="tagline">Revolutionizing IT Services</div>
      </div>
    </div>
  </section>

  <section class="card card--back" aria-label="Card back">
    <svg class="back-art" viewBox="0 0 700 400" aria-hidden="true">
      <polygon points="0,180 110,130 240,230 260,400 0,400" fill="var(--band-grey)"/>
      <polygon points="0,240 120,190 150,400 0,400" fill="var(--card-white)" opacity="0"/>
    </svg>
    <svg class="back-art" viewBox="0 0 700 400" role="img" aria-label="Large brand cube decoration">
      <polygon points="70,210 200,140 330,210 330,370 200,400 70,330" fill="var(--brand-blue-pale)"/>
    </svg>
    <div class="corner-tab"></div>
    <div class="back-info">
      <div class="brand-name">Quillbrook Networks Ltd.</div>
      <div class="person-name">MARTA ELLISON</div>
      <div class="person-role">DIRECTOR</div>
      <ul class="contact-list">
        <li>604-555-0148
          <svg viewBox="0 0 12 12"><path d="M3 1 L5 3.5 L4 5 Q5 7 7 8 L8.5 7 L11 9 L9.5 11 Q4 10.5 1 3 Z" fill="none" stroke="var(--brand-blue)" stroke-width="1.2"/></svg>
        </li>
        <li>info@martaellison.com
          <svg viewBox="0 0 12 12"><rect x="1" y="2.5" width="10" height="7" fill="none" stroke="var(--brand-blue)" stroke-width="1.2"/><path d="M1 2.5 L6 6.5 L11 2.5" fill="none" stroke="var(--brand-blue)" stroke-width="1.2"/></svg>
        </li>
        <li>www.quillbrook.me
          <svg viewBox="0 0 12 12"><circle cx="6" cy="6" r="5" fill="none" stroke="var(--brand-blue)" stroke-width="1.2"/><path d="M1 6 H11 M6 1 Q3 6 6 11 Q9 6 6 1" fill="none" stroke="var(--brand-blue)" stroke-width="1"/></svg>
        </li>
      </ul>
    </div>
  </section>

</main>
</body>
</html>
```